Tour operator needs simple coded WordPress site (updated extra payment for coding and guaranteed)

[update 9/7/2015]
If you design a new logo and it gets accepted, even if we use another template with your logo you will get $50
[update 8/7/2015]
Update on questions about dual-language
For dual languages we are happy to set up a second site with the same designs in a second language.
For the design aspect just allow the user to switch between languages with an icon.
For the coding, a replica of the site on a second server will do (to save messing around with multiple language plugins) - we will populate it with Chinese text
[original post]
Simple coded WordPress site for tours
You can choose to design only or design and code ($340 design, $150 bonus for coding)
Open design brief - use your creativity
Will be in 2 languages (English and Chinese) but design needs only to be in one language
Winning design will be chosen only from home page, but the winner must make a second standard template page when chosen at no extra cost.
Must be responsive design
We only need homepage and standard template page design and coding, we will populate the pages
You can use design ideas from our pamphlet if you like - attached
Only a sample logo and colors on website and pamphlet - feel free to change as the current ones seem restrictive
Current website framework only to give an idea of the number of pages and basic menu structure (no need to use existing navigation style or any style at all for that matter, open brief)
http://brightwattlejourneys.com.au/
Target Market(s)
Chinese parents of kids 10-14 (the kids will take the tour)
Industry/Entity Type
Tour
Number of Pages Required
2 page
Look and feel
Each slider illustrates characteristics of the customer's brand and the style your logo design should communicate.

```html
<!DOCTYPE html>
<html lang="en">
<head>
<meta charset="utf-8">
<title>Bright Wattle Journeys</title>
<link href="https://fonts.googleapis.com/css2?family=Lato:wght@400;700&family=Oswald:wght@400&display=swap" rel="stylesheet">
<style>
:root{
  --navy:#2f3e80;
  --gold:#f4ab1c;
  --ink:#2b2b2b;
  --text:#555;
  --line:#cfcfcf;
  --grey-bg:#eeeeee;
  --footer:#1e1e1e;
  --white:#fff;
}
*{box-sizing:border-box;margin:0;padding:0}
html,body{width:926px;height:1200px;overflow:hidden}
body{position:relative;font-family:'Lato',sans-serif;color:var(--text);background:var(--white)}
.abs{position:absolute}
.hero{left:0;top:0;width:926px;height:476px;background:linear-gradient(160deg,#8d8f96 0%,#5d5f66 40%,#4a4a50 70%,#6e6a66 100%)}
.hero-glow{left:0;top:0;width:360px;height:130px;background:radial-gradient(ellipse at 40% 45%,rgba(255,255,255,.85) 0%,rgba(255,255,255,.4) 45%,rgba(255,255,255,0) 75%)}
.brand{left:108px;top:38px;display:flex;align-items:center;gap:10px}
.brand-dot{width:44px;height:44px;border-radius:50%;background:var(--navy)}
.brand-name{font-family:'Lato',sans-serif;font-weight:700;font-size:24px;color:var(--navy);line-height:1}
.lang{left:748px;top:15px;width:78px;height:25px;border:2px solid var(--white);color:var(--white);font-weight:700;font-size:12px;display:flex;align-items:center;padding-left:9px;gap:10px}
.tagline{right:102px;top:362px;text-align:right;font-family:'Oswald',sans-serif;color:var(--white);font-size:21px;line-height:28px;text-transform:uppercase}
.nav{left:0;top:428px;width:926px;height:48px;border-top:1px solid rgba(255,255,255,.5);background:rgba(40,40,50,.25)}
.nav a{position:absolute;top:0;height:48px;line-height:48px;color:var(--white);font-weight:700;font-size:12px;text-decoration:none;text-align:center}
.nav a.active{background:var(--white);color:var(--navy)}
.social{position:absolute;top:9px;width:30px;height:30px;border-radius:50%;border:2px solid var(--white)}
h2.title{font-family:'Oswald',sans-serif;font-weight:400;font-size:21px;color:var(--ink);text-transform:uppercase;line-height:1}
.navy{color:var(--navy)}.gold{color:var(--gold)}
.welcome{left:102px;top:525px;width:455px}
.welcome .rule{height:1px;background:var(--line);margin:10px -1px 10px}
.lead{font-weight:700;font-size:12px;line-height:15px;color:#444;margin-bottom:5px}
.body{font-size:10px;line-height:13.5px;margin-bottom:5px}
.btn{background:var(--navy);color:var(--white);font-weight:700;font-size:13px;display:flex;align-items:center;justify-content:center;text-transform:uppercase}
.vrule{left:575px;top:506px;width:1px;height:210px;background:var(--line)}
.field{position:absolute;left:598px;width:227px;border:1px solid #c8c8c8;font-size:11px;color:#999;padding:6px 7px}
.features{left:0;top:733px;width:926px;height:380px;background:var(--grey-bg)}
.card{position:absolute;top:771px;width:348px;height:305px;background:var(--white);border:1px solid #d5d5d5;border-top:2px solid var(--gold);padding:15px 14px}
.card-head{display:flex;align-items:flex-end;gap:9px;margin-bottom:9px}
.card-head h3{flex:1;font-family:'Oswald',sans-serif;font-weight:400;font-size:17px;color:var(--navy);text-transform:uppercase;border-bottom:1px dotted #999;padding-bottom:2px;line-height:1.2}
.card ul{list-style:none}
.card li{display:flex;gap:8px;font-size:10px;line-height:13px;margin-bottom:7px}
.card li svg{flex:none;margin-top:1px}
.newsletter{left:0;top:1113px;width:926px;height:43px;background:var(--navy);color:var(--white)}
.footer{left:0;top:1156px;width:926px;height:44px;background:var(--footer);color:var(--white);font-size:10px}
</style>
</head>
<body>
<div class="abs hero" role="img" aria-label="Group of smiling students posing by a harbour bridge"></div>
<div class="abs hero-glow"></div>
<div class="abs brand"><span class="brand-dot"></span><span class="brand-name">bright wattle</span></div>
<div class="abs lang">English
  <svg width="11" height="7" viewBox="0 0 11 7"><path d="M1 1l4.5 4.5L10 1" fill="none" stroke="#fff" stroke-width="1.6"/></svg></div>
<svg class="abs" style="left:62px;top:199px" width="40" height="78" viewBox="0 0 40 78"><path d="M39 1L1 39l38 38" fill="none" stroke="#fff" stroke-width="1"/></svg>
<svg class="abs" style="left:826px;top:199px" width="40" height="78" viewBox="0 0 40 78"><path d="M1 1l38 38L1 77" fill="none" stroke="#fff" stroke-width="1"/></svg>
<div class="abs tagline">Educational, safe, culturally enlightening<br>Australian journeys full of fun.</div>
<nav class="abs nav">
  <a class="active" href="#" style="left:101px;width:112px">Home</a>
  <a href="#" style="left:226px;width:100px">About Us</a>
  <a href="#" style="left:346px;width:100px">Tours</a>
  <a href="#" style="left:470px;width:100px">Contact Us</a>
  <span class="social" style="left:714px"></span>
  <span class="social" style="left:754px"></span>
  <span class="social" style="left:794px"></span>
</nav>

<section class="abs welcome">
  <h2 class="title">Welcome to <span class="navy">Bright</span> <span class="gold">Wattle</span> <span class="navy">Journeys</span></h2>
  <div class="rule"></div>
  <p class="lead">At Bright Wattle Journeys we are passionate about educational travel and opportunities for students to gain academic and cultural understanding of Australia.</p>
  <p class="body">14 day premium cultural and educational tours to Australian cities. Educational, safe, culturally enlightening and fun. Learn about educational institutions, history, sports, laws and customs, food and culture while improving your English.</p>
  <p class="body">At Bright Wattle Journeys we are passionate about educational travel and providing opportunities for students to learn more about a country and gain a deeper understanding of the culture. The out of classroom experience gained on our trips is invaluable.</p>
</section>
<div class="abs btn" style="left:451px;top:690px;width:105px;height:26px">Read More</div>
<div class="abs vrule"></div>
<h2 class="abs title" style="left:598px;top:525px">Quick Inquiry</h2>
<div class="field" style="top:561px;height:26px">Name</div>
<div class="field" style="top:593px;height:26px">Email</div>
<div class="field" style="top:626px;height:57px">Message</div>
<div class="abs btn" style="left:720px;top:690px;width:105px;height:26px">Submit</div>

<div class="abs features"></div>
<div class="card" style="left:101px">
  <div class="card-head">
    <svg width="30" height="20" viewBox="0 0 30 20"><path d="M15 2L1 8l14 6 14-6z" fill="var(--gold)"/><path d="M7 11v5c4 3 12 3 16 0v-5l-8 3.5z" fill="var(--gold)"/></svg>
    <h3>Educational and Cultural</h3>
  </div>
  <ul>
    <li><svg width="17" height="11" viewBox="0 0 17 11"><path d="M0 10C3 4 7 3 11 3V0l6 5-6 5V7C7 7 3 8 0 10z" fill="var(--navy)"/></svg>Professional lecturers from Sydney universities</li>
    <li><svg width="17" height="11" viewBox="0 0 17 11"><path d="M0 10C3 4 7 3 11 3V0l6 5-6 5V7C7 7 3 8 0 10z" fill="var(--navy)"/></svg>2 hour lessons every day in easy to understand,<br>high-quality English</li>
    <li><svg width="17" height="11" viewBox="0 0 17 11"><path d="M0 10C3 4 7 3 11 3V0l6 5-6 5V7C7 7 3 8 0 10z" fill="var(--navy)"/></svg>Subjects from the Australian Educational Curriculum as well as cultural information on Australia</li>
    <li><svg width="17" height="11" viewBox="0 0 17 11"><path d="M0 10C3 4 7 3 11 3V0l6 5-6 5V7C7 7 3 8 0 10z" fill="var(--navy)"/></svg>How to live, get around, shop and socialise in Australia</li>
    <li><svg width="17" height="11" viewBox="0 0 17 11"><path d="M0 10C3 4 7 3 11 3V0l6 5-6 5V7C7 7 3 8 0 10z" fill="var(--navy)"/></svg>Attitudes to languages, food, religion and culture</li>
    <li><svg width="17" height="11" viewBox="0 0 17 11"><path d="M0 10C3 4 7 3 11 3V0l6 5-6 5V7C7 7 3 8 0 10z" fill="var(--navy)"/></svg>Outdoor activities and sport</li>
  </ul>
</div>
<div class="card" style="left:477px">
  <div class="card-head">
    <svg width="30" height="24" viewBox="0 0 30 24"><path d="M9 10V7a6 6 0 0112 0" fill="none" stroke="var(--gold)" stroke-width="3" transform="translate(-6 0)"/><rect x="0" y="10" width="18" height="14" rx="2" fill="var(--gold)"/><circle cx="9" cy="16" r="2" fill="#fff"/></svg>
    <h3>Safe and Secure</h3>
  </div>
  <ul>
    <li><svg width="17" height="11" viewBox="0 0 17 11"><path d="M0 10C3 4 7 3 11 3V0l6 5-6 5V7C7 7 3 8 0 10z" fill="var(--navy)"/></svg>Staff certified by the government for Working With Children</li>
    <li><svg width="17" height="11" viewBox="0 0 17 11"><path d="M0 10C3 4 7 3 11 3V0l6 5-6 5V7C7 7 3 8 0 10z" fill="var(--navy)"/></svg>Staff certified in first aid care</li>
    <li><svg width="17" height="11" viewBox="0 0 17 11"><path d="M0 10C3 4 7 3 11 3V0l6 5-6 5V7C7 7 3 8 0 10z" fill="var(--navy)"/></svg>Professional accommodation with excellent history in caring for children with extremely well documented Safety Management Procedures including;</li>
    <li><svg width="17" height="11" viewBox="0 0 17 11"><path d="M0 10C3 4 7 3 11 3V0l6 5-6 5V7C7 7 3 8 0 10z" fill="var(--navy)"/></svg>Safety Management - reducing risk when taking students out of the classroom</li>
    <li><svg width="17" height="11" viewBox="0 0 17 11"><path d="M0 10C3 4 7 3 11 3V0l6 5-6 5V7C7 7 3 8 0 10z" fill="var(--navy)"/></svg>Safety &amp; Emergency Procedures (Location-specific)</li>
    <li><svg width="17" height="11" viewBox="0 0 17 11"><path d="M0 10C3 4 7 3 11 3V0l6 5-6 5V7C7 7 3 8 0 10z" fill="var(--navy)"/></svg>Standard Operating Procedures</li>
    <li><svg width="17" height="11" viewBox="0 0 17 11"><path d="M0 10C3 4 7 3 11 3V0l6 5-6 5V7C7 7 3 8 0 10z" fill="var(--navy)"/></svg>Activity-Specific Risk Management Matrix</li>
    <li><svg width="17" height="11" viewBox="0 0 17 11"><path d="M0 10C3 4 7 3 11 3V0l6 5-6 5V7C7 7 3 8 0 10z" fill="var(--navy)"/></svg>Area Assessment Documentation</li>
    <li><svg width="17" height="11" viewBox="0 0 17 11"><path d="M0 10C3 4 7 3 11 3V0l6 5-6 5V7C7 7 3 8 0 10z" fill="var(--navy)"/></svg>Medical Form, Dietary Requirements Form, First Aid Incident &amp; Management Forms</li>
    <li><svg width="17" height="11" viewBox="0 0 17 11"><path d="M0 10C3 4 7 3 11 3V0l6 5-6 5V7C7 7 3 8 0 10z" fill="var(--navy)"/></svg>Clothing &amp; Equipment List</li>
  </ul>
</div>

<section class="abs newsletter">
  <svg class="abs" style="left:101px;top:5px" width="34" height="34" viewBox="0 0 34 34"><circle cx="17" cy="17" r="15.5" fill="none" stroke="#fff" stroke-width="2"/><circle cx="17" cy="17" r="11" fill="#fff"/><rect x="11" y="13" width="12" height="8" fill="var(--navy)"/><path d="M11 13l6 5 6-5" fill="none" stroke="#fff" stroke-width="1"/></svg>
  <div class="abs" style="left:145px;top:9px;font-size:19px">Newsletter Signup</div>
  <svg class="abs" style="left:344px;top:4px" width="28" height="36" viewBox="0 0 28 36"><path d="M1 1l16 17L1 35M9 1l16 17L9 35" fill="none" stroke="#fff" stroke-width="1.3"/></svg>
  <div class="abs" style="left:390px;top:15px;font-size:12px">Signup For Free Email Updates</div>
  <div class="abs" style="left:572px;top:12px;width:188px;height:21px;background:#fff;color:#333;font-size:10px;padding:4px 7px">Enter your email here</div>
  <div class="abs" style="left:767px;top:12px;width:58px;height:21px;background:#111;border:1px solid #555;font-weight:700;font-size:10px;display:flex;align-items:center;justify-content:center">SUBMIT</div>
</section>
<footer class="abs footer">
  <div class="abs" style="left:102px;top:15px">Home &nbsp;|&nbsp; About Us &nbsp;|&nbsp; Tours &nbsp;|&nbsp; Contact Us</div>
  <div class="abs" style="right:103px;top:15px">© 2015 BRIGHT WATTLE JOURNEYS. &nbsp;|&nbsp; All Rights Reserved.</div>
</footer>
</body>
</html>
```